Virtual Racing Community for Runners Needs a Refreshed Web Design

We are a STARTUP. The current website consists of 3 main pages that function well; however, they are not producing the proper conversions because we need a more professional look and better execution of our great ideas.

First page: landing page that needs to be intriguing, sleek, create urgency, incorporate our call to action and most importantly get the consumer to click a button to get to second page. www.lomberun.com

Second page: sign up page that incorporates our already existing postwren form that doesn't take the viewer away from the page on incorrect form field entry. On successful completion needs to inform the viewer to check the email and confirm (possibly in spam) and open third page. http://www.lomberun.com/beta.html

Third page: preorder page that allows the user prepurchase through a well working form through "www.getparsnip.com." This interface works really well; however, the graphics and page need to really entice the viewer to buy. http://www.lomberun.com/preorder.html

And that's it!!! Simple 3 pages that function currently 95% how we want it, but really needs that creative touch to push it to the next level!

Contact us with any other questions!
Updates

Project Deadline Extended
Reason: I have provided numerous feedback and am awaiting redesigns. Have it narrowed down to 2 designers. Need time to vet with stakeholders.

Industry/Entity Type

Racing

```html
<!DOCTYPE html>
<html lang="en">
<head>
<meta charset="utf-8">
<title>Lomberun — Race on your own terms</title>
<link href="https://fonts.googleapis.com/css2?family=Oswald:wght@400;500;600&family=Arimo:wght@400;700&display=swap" rel="stylesheet">
<style>
:root{
  --red:#b41f1a;
  --orange:#d97a18;
  --black:#111111;
  --ink:#141414;
  --grey:#444444;
  --white:#ffffff;
  --footer:#131313;
}
*{box-sizing:border-box;margin:0;padding:0}
html,body{width:1200px;height:1053px;overflow:hidden;background:var(--white)}
body{position:relative;font-family:"Arimo",Arial,sans-serif;color:var(--grey)}
.hero{position:absolute;left:0;top:0;width:1200px;height:522px;
  background:radial-gradient(ellipse at 85% 35%,#fff6dc 0%,#f6c777 25%,#e7a04a 50%,#b56a33 75%,#6b4030 100%)}
.hero-text{position:absolute;left:605px;top:25px;width:560px}
.brand{font-family:"Oswald",sans-serif;font-weight:600;font-size:80px;line-height:96px;letter-spacing:3px;color:var(--ink)}
.headline{font-family:"Oswald",sans-serif;font-weight:500;font-size:44px;line-height:54px;color:var(--ink);margin-top:18px;letter-spacing:-.3px}
.tagline{font-family:"Oswald",sans-serif;font-weight:400;font-size:32px;line-height:40px;color:var(--ink);letter-spacing:.4px}
.event-title{font-family:"Oswald",sans-serif;font-weight:500;font-size:32px;line-height:40px;color:var(--white);margin-top:46px}
.event-copy{font-size:14px;line-height:17px;color:var(--white);margin:6px 0 0 3px;width:370px}
.register{position:absolute;left:605px;top:375px;display:flex;height:54px;text-decoration:none}
.register .arrow{width:60px;background:var(--black);display:flex;align-items:center;justify-content:center}
.register .label{width:193px;background:var(--red);color:var(--white);font-family:"Oswald",sans-serif;font-weight:500;font-size:28px;display:flex;align-items:center;justify-content:center}
.card{position:absolute;left:110px;top:486px;width:980px;height:314px;background:var(--white);box-shadow:0 6px 18px rgba(0,0,0,.12)}
.news{display:flex;height:104px;background:var(--red);color:var(--white)}
.date{flex:none;width:98px;background:var(--orange);display:flex;flex-direction:column;align-items:center;padding-top:16px}
.date .day{width:44px;height:44px;border:2px solid var(--white);border-radius:50%;display:flex;align-items:center;justify-content:center;font-family:"Oswald",sans-serif;font-size:22px}
.date .month{font-size:14px;margin-top:6px}
.news-body{padding:14px 30px 14px 16px}
.news-body h2{font-weight:400;font-size:18px;margin-bottom:10px}
.news-body p{font-size:13px;line-height:16px}
.features{position:absolute;top:172px;left:0;width:980px}
.feature{position:absolute;top:0;width:300px;height:120px;--indent:60px}
.feature-icon{position:absolute;left:0;top:0}
.feature h3{margin-left:var(--indent);font-weight:400;font-size:18px;color:#333;line-height:22px}
.feature p{margin:2px 0 0 calc(var(--indent) + 1px);width:232px;font-size:13px;line-height:15.5px;color:#444}
.view{position:absolute;left:var(--indent);top:86px;display:flex;height:25px;text-decoration:none}
.view .label{width:49px;background:var(--red);color:var(--white);font-size:12px;display:flex;align-items:center;justify-content:center}
.view .arrow{width:28px;background:var(--black);display:flex;align-items:center;justify-content:center}
.footer{position:absolute;left:0;top:862px;width:1200px;height:128px;background:var(--footer)}
.connect{position:absolute;left:113px;top:28px;font-family:"Oswald",sans-serif;font-size:21px;line-height:30px;color:var(--white)}
.social{position:absolute;left:115px;top:72px;display:flex;gap:20px}
.social span{width:40px;height:40px;border:2px solid var(--white);border-radius:50%}
.contact{position:absolute;left:829px;top:32px;color:#ddd}
.contact .row{display:flex;align-items:center;gap:12px}
.contact .icon{width:32px;height:32px;border:2px solid var(--white);border-radius:50%;display:flex;align-items:center;justify-content:center}
.address{font-size:12px;line-height:18px}
.phone{font-size:24px;color:#ccc}
.legal{position:absolute;left:0;top:990px;width:1200px;height:48px;background:var(--orange);color:var(--white);font-size:11px}
.legal .copy{position:absolute;left:116px;top:18px}
.legal .links{position:absolute;right:115px;top:18px}
.base{position:absolute;left:0;top:1038px;width:1200px;height:15px;background:var(--footer)}
</style>
</head>
<body>
<div class="hero" role="img" aria-label="Close-up photo of a runner's legs and red running shoes on a road in warm golden sunlight"></div>
<header class="hero-text">
  <div class="brand">LOMBERUN</div>
  <h1 class="headline">RACE ON YOUR OWN TERMS</h1>
  <div class="tagline">WHEREVER. WHATEVER. WHENEVER.</div>
  <h2 class="event-title">CHICAGO BETA RUN WEEK 2</h2>
  <p class="event-copy">For a limited time be the first to receive early access and receive a Real Life Beta Tester t-shirt.</p>
</header>
<a class="register" href="#">
  <span class="arrow"><svg width="26" height="20" viewBox="0 0 26 20"><path d="M2 10h20M14 2l8 8-8 8" stroke="#fff" stroke-width="3" fill="none"/></svg></span>
  <span class="label">REGISTER NOW</span>
</a>

<section class="card">
  <div class="news">
    <div class="date"><span class="day">23</span><span class="month">AUG</span></div>
    <div class="news-body">
      <h2>Latest Virtual Run</h2>
      <p>Lorem ipsum dolor sit amet, consectetur adipisicing elit, sed do eiusmod tempor incididunt ut labore et dolore magna aliqua. Ut enim ad minim veniam, quis nostrud exercitation ullamco laboris nisi ut aliquip ex ea commodo consequat.</p>
    </div>
  </div>
  <div class="features">
    <div class="feature" style="left:25px;--indent:59px">
      <svg class="feature-icon" width="44" height="44" viewBox="0 0 44 44"><path d="M12 4h20v10a10 10 0 0 1-20 0z" fill="#333"/><path d="M12 7H4c0 8 5 11 9 11M32 7h8c0 8-5 11-9 11" stroke="#333" stroke-width="3" fill="none"/><rect x="19" y="24" width="6" height="8" fill="#333"/><rect x="12" y="32" width="20" height="8" fill="#333"/></svg>
      <h3>freebies and giveaways</h3>
      <p>Duis aute irure dolor in reprehenderit in voluptate velit esse cillum dolore eu fugiat nulla pariatur.</p>
      <a class="view" href="#"><span class="label">view</span><span class="arrow"><svg width="12" height="10" viewBox="0 0 12 10"><path d="M1 5h9M6 1l4 4-4 4" stroke="#fff" stroke-width="1.6" fill="none"/></svg></span></a>
    </div>
    <div class="feature" style="left:345px;--indent:62px">
      <svg class="feature-icon" width="50" height="50" viewBox="0 0 50 50"><circle cx="24" cy="26" r="16" stroke="#333" stroke-width="4" fill="none"/><rect x="20" y="4" width="8" height="5" fill="#333"/><path d="M24 26V16M24 26l7 5" stroke="#333" stroke-width="3"/></svg>
      <h3>run at your own pace</h3>
      <p>You can walk, jog, skip or run the distance of your choice. You can complete your race at the gym ...</p>
      <a class="view" href="#"><span class="label">view</span><span class="arrow"><svg width="12" height="10" viewBox="0 0 12 10"><path d="M1 5h9M6 1l4 4-4 4" stroke="#fff" stroke-width="1.6" fill="none"/></svg></span></a>
    </div>
    <div class="feature" style="left:668px;--indent:67px">
      <svg class="feature-icon" width="52" height="50" viewBox="0 0 52 50"><circle cx="17" cy="12" r="10" stroke="#333" stroke-width="3" fill="#fff"/><circle cx="38" cy="22" r="11" fill="#333"/><circle cx="16" cy="32" r="13" stroke="#333" stroke-width="4" fill="#fff"/><text x="16" y="38" font-family="Arimo,sans-serif" font-weight="700" font-size="16" text-anchor="middle" fill="#333">$</text><text x="38" y="28" font-family="Arimo,sans-serif" font-weight="700" font-size="14" text-anchor="middle" fill="#fff">$</text><text x="17" y="17" font-family="Arimo,sans-serif" font-weight="700" font-size="12" text-anchor="middle" fill="#333">$</text></svg>
      <h3>discounts</h3>
      <p>If you have 10 or more runners interested in participating in one of our races, please contact us and ...</p>
      <a class="view" href="#"><span class="label">view</span><span class="arrow"><svg width="12" height="10" viewBox="0 0 12 10"><path d="M1 5h9M6 1l4 4-4 4" stroke="#fff" stroke-width="1.6" fill="none"/></svg></span></a>
    </div>
  </div>
</section>

<footer class="footer">
  <div class="connect">CONNECT WITH US</div>
  <div class="social" aria-label="Social links"><span></span><span></span><span></span><span></span></div>
  <div class="contact">
    <div class="row">
      <span class="icon"><svg width="18" height="16" viewBox="0 0 18 16"><path d="M9 1L1 8h2.5v7h4v-4h3v4h4V8H17z" fill="#fff"/></svg></span>
      <span class="address">4410 Larkfield Avenue Studio 36<br>Harbor Lane, Easton 204518</span>
    </div>
    <div class="row" style="margin-top:6px">
      <span class="icon"><svg width="16" height="16" viewBox="0 0 16 16"><path d="M3 1l3 3-2 2c1 2 3 4 5 5l2-2 3 3-2 3C7 14 2 9 1 3z" fill="#fff"/></svg></span>
      <span class="phone">014-552-3870</span>
    </div>
  </div>
</footer>
<div class="legal">
  <span class="copy">© Copyright 2014 Lomberun. All Rights Reserved</span>
  <span class="links">Policy | Terms</span>
</div>
<div class="base"></div>
</body>
</html>
```